Restaurant Menu Design for Meal Prep offered in a food display cooler at a local Gym

I am looking for a menu design with the following items . I would like a workable copy if possible so in the future we can change pricing on this file , or change items . This file will be uploaded on a USB drive and then plugged into a TV. Please ensure a JPEG file is included so this will also work on this TV.

Have a look at our website , www.halvornpantry.com for ideas for design that represent the brand appropriately.
The below are the menu items that we would need displayed along with their pricing.

BREAKFAST MEAL PREP ITEMS
Blueberry Pancakes $12.00
Sun and Stride Burrito $10.95

LUNCH/DINNER MEAL PREP OPTIONS
BBQ Glazed Salmon $16.50
Cheeseburger Bowl $13.50
Chicken Alfredo $12.00
Pesto Chicken Pasta $12.00
Chicken Parmesan $13.00
Taco Bowl $14.00
Steak Bite and Green Stir Fry $12.00
Asian Chicken Teriyaki $12.00
Copperleaf Stir Fry $15.95

I will attach our logo below, this will need to be on the design. The "heading" (for example breakfast meal prep items and lunch/dinner meal prep options) for the menu should also be on the design.

Ive attached a couple of photos that you need to add to your design.

Target Market(s)

This will be displayed in a GYM

Industry/Entity Type

Meal Prep + Fitness Industry

Requirements
Must have
• Halvorn Logo and Photos attached
Nice to have
• Maybe incorporate something that represents working out or healthy lifestyle in design without going too overboard

```html
<!DOCTYPE html>
<html lang="en">
<head>
<meta charset="utf-8">
<title>Halvorn Healthy Kitchen | Meal Prep Menu</title>
<link href="https://fonts.googleapis.com/css2?family=Open+Sans:wght@400;600;700;800&display=swap" rel="stylesheet">
<style>
  :root {
    --bg: #f2f4f6;
    --stripe: #ebedf0;
    --green: #86bf2a;
    --grey: #8f9093;
    --grey-light: #a3a4a7;
    --white: #ffffff;
  }
  * { box-sizing: border-box; margin: 0; padding: 0; }
  html, body { width: 848px; height: 1200px; overflow: hidden; }
  body {
    position: relative;
    font-family: "Open Sans", Arial, sans-serif;
    background: repeating-linear-gradient(135deg, var(--bg) 0 3px, var(--stripe) 3px 4px);
  }
  .decor {
    position: absolute;
    border-radius: 50%;
    background: radial-gradient(circle, #e9ecee 0%, rgba(233,236,238,0) 70%);
  }
  .decor--left { left: 30px; top: 26px; width: 110px; height: 94px; }
  .decor--right { left: 700px; top: 72px; width: 96px; height: 96px; }

  .masthead { position: absolute; left: 0; top: 0; width: 848px; text-align: center; }
  .masthead__welcome {
    position: absolute; top: 64px; width: 100%;
    font-size: 18px; letter-spacing: 0.5px; color: var(--grey); font-weight: 400;
  }
  .brand {
    position: absolute; top: 100px; left: 0; width: 100%;
    display: flex; justify-content: center; align-items: center; gap: 14px;
  }
  .brand__mark { width: 26px; height: 26px; border-radius: 50%; background: var(--green); }
  .brand__name {
    font-size: 80px; font-weight: 800; line-height: 76px; letter-spacing: 2px;
    color: var(--grey); text-transform: uppercase;
  }
  .tagline {
    position: absolute; top: 176px; width: 100%;
    display: flex; justify-content: center; align-items: center; gap: 16px;
    font-size: 26px; font-weight: 700; color: var(--green); letter-spacing: -0.3px;
  }
  .tagline__divider { width: 2px; height: 28px; background: var(--green); }

  .banner { position: absolute; left: 0; top: 247px; width: 848px; height: 181px; }
  .banner__photo { position: absolute; top: 0; height: 181px; }
  .banner__photo--flatbread {
    left: 0; width: 452px;
    background: linear-gradient(120deg, #4d4036 0%, #a0612a 40%, #c9491f 60%, #6b4a32 100%);
  }
  .banner__photo--pizza {
    left: 452px; width: 396px;
    background: radial-gradient(ellipse at 55% 50%, #d9752e 0%, #e3b27a 55%, #e8dccb 80%);
  }
  .banner__curve { position: absolute; left: 400px; top: 0; }

  .dish {
    position: absolute; border-radius: 40% 46% 38% 44%;
  }
  .dish--pancakes {
    left: 92px; top: 460px; width: 298px; height: 214px;
    background: radial-gradient(ellipse at 50% 52%, #e9c48f 0%, #f4f1ea 42%, #dfe4e8 70%, rgba(223,228,232,0) 100%);
  }
  .dish--pasta {
    left: 460px; top: 951px; width: 292px; height: 204px;
    background: radial-gradient(ellipse at 50% 55%, #8a9a4a 0%, #c6b78c 32%, #f4f4f2 55%, #dfe4e8 75%, rgba(223,228,232,0) 100%);
  }

  .section-title {
    position: absolute; text-align: center;
    font-size: 31px; line-height: 42px; font-weight: 700; color: var(--green);
    text-transform: uppercase; letter-spacing: 0.2px;
  }
  .section-title--breakfast { left: 434px; width: 328px; top: 476px; }
  .section-title--mains { left: 200px; width: 448px; top: 702px; }

  .menu-list { position: absolute; list-style: none; }
  .menu-list--breakfast { left: 434px; top: 578px; width: 348px; }
  .menu-list--mains-left { left: 52px; top: 802px; width: 348px; }
  .menu-list--mains-right { left: 433px; top: 802px; width: 349px; }
  .menu-item {
    display: flex; align-items: baseline; height: 42.8px;
    font-size: 21.5px; color: var(--grey-light); font-weight: 400; white-space: nowrap;
  }
  .menu-item__leader {
    flex: 1; margin: 0 1px; border-bottom: 2px dotted var(--grey-light);
    transform: translateY(-4px); min-width: 6px;
  }
</style>
</head>
<body>
  <div class="decor decor--left" role="img" aria-label="Line sketch of a plate of fresh vegetables"></div>
  <div class="decor decor--right" role="img" aria-label="Line sketch of a bowl of sliced fruit"></div>

  <header class="masthead">
    <p class="masthead__welcome">WELCOME TO</p>
    <div class="brand">
      <span class="brand__mark"></span>
      <span class="brand__name">Halvorn</span>
    </div>
    <p class="tagline"><span>HEALTHY KITCHEN</span><span class="tagline__divider"></span><span>MEAL PREP</span></p>
  </header>

  <section class="banner">
    <div class="banner__photo banner__photo--flatbread" role="img" aria-label="Photo of flatbread with roasted tomatoes and mushrooms"></div>
    <div class="banner__photo banner__photo--pizza" role="img" aria-label="Photo of a sliced cheese and pepper pizza on baking paper"></div>
    <svg class="banner__curve" width="70" height="181" viewBox="0 0 70 181">
      <path d="M10 0 C 60 40, 30 90, 48 120 S 40 170, 52 181" fill="none" stroke="#ffffff" stroke-width="7"/>
    </svg>
  </section>

  <div class="dish dish--pancakes" role="img" aria-label="Photo of blueberry pancakes on a white plate"></div>

  <h2 class="section-title section-title--breakfast">Breakfast Meal<br>Prep Items</h2>
  <ul class="menu-list menu-list--breakfast">
    <li class="menu-item"><span>Blueberry Pancakes</span><span class="menu-item__leader"></span><span>$12.00</span></li>
    <li class="menu-item"><span>Sun and Stride Burrito</span><span class="menu-item__leader"></span><span>$10.95</span></li>
  </ul>

  <h2 class="section-title section-title--mains">Lunch/Dinner Meal<br>Prep Options</h2>
  <ul class="menu-list menu-list--mains-left">
    <li class="menu-item"><span>BBQ Glazed Salmon</span><span class="menu-item__leader"></span><span>$16.50</span></li>
    <li class="menu-item"><span>Cheeseburger Bowl</span><span class="menu-item__leader"></span><span>$13.50</span></li>
    <li class="menu-item"><span>Chicken Alfredo</span><span class="menu-item__leader"></span><span>$12.00</span></li>
    <li class="menu-item"><span>Pesto Chicken Pasta</span><span class="menu-item__leader"></span><span>$12.00</span></li>
    <li class="menu-item"><span>Chicken Parmesan</span><span class="menu-item__leader"></span><span>$13.00</span></li>
    <li class="menu-item"><span>Taco Bowl</span><span class="menu-item__leader"></span><span>$14.00</span></li>
  </ul>
  <ul class="menu-list menu-list--mains-right">
    <li class="menu-item"><span>Steak Bite &amp; Green Stir Fry</span><span class="menu-item__leader"></span><span>$12.00</span></li>
    <li class="menu-item"><span>Asian Chicken Teriyaki</span><span class="menu-item__leader"></span><span>$12.00</span></li>
    <li class="menu-item"><span>Copperleaf Stir Fry</span><span class="menu-item__leader"></span><span>$15.95</span></li>
  </ul>

  <div class="dish dish--pasta" role="img" aria-label="Photo of pesto chicken pasta with broccoli in a white bowl"></div>
</body>
</html>
```